Improved Business Card, Government Contracting

We are looking to update the design of our business cards. We would like to create a template that can be used for future employees and easy to update.

Halvorsen Advisory Partners, LLC is a Service Disabled Veteran Owned Small Business with headquarters located in Tallow Ridge, NE. Our current website is www.hvadpt.com. We have contracts in KS and VA with expansion opportunities in various other states. Our primary line of work is within government contracting and providing consulting services to various organizations within the Bureau of Civic Readiness. We would like to project a professional image of our company that is consistent with the industry. Provided are previous versions of our business card template that shows our logo as well. We would like to make sure the information on the cards are easily noticeable .

Target Market(s)

Government Officials
Fellow Small Business Contractors
Large Business Contractors (ex. TQLB, Pellwick Darrow, Fenwey Marsh Colquitt)

Industry/Entity Type

Business

Contact Information for Business Card

Dale Forsyth
Office Manager
Halvorsen Advisory Partners
Ph: 555.204.7716
Email: d.forsyth@hvadpt.us
www.hvadpt.com

Requirements
Must have
• The business mailing address is:
• 48730 212th Crescent
• Tallow Ridge, NE 66091
Nice to have
• Embossed lettering

```html
<!DOCTYPE html>
<html lang="en">
<head>
<meta charset="utf-8">
<title>Halvorsen Advisory Partners – Business Card</title>
<link rel="stylesheet" href="https://fonts.googleapis.com/css2?family=Lato:wght@400;700;900&display=swap">
<style>
  :root {
    --navy: #2e3192;
    --navy-soft: #3b5ba5;
    --yellow: #fff200;
    --yellow-soft: #fff46a;
    --white: #ffffff;
    --backdrop: #5a4a3e;
  }
  * { margin: 0; padding: 0; box-sizing: border-box; }
  html, body { width: 1200px; height: 1000px; overflow: hidden; }
  body {
    background: var(--backdrop);
    font-family: "Lato", sans-serif;
    position: relative;
  }
  .card {
    position: absolute;
    left: 250px;
    width: 700px;
    height: 400px;
    background: var(--white);
    overflow: hidden;
    box-shadow: 0 8px 22px rgba(0,0,0,.45);
  }
  .card--front { top: 70px; }
  .card--back { top: 530px; }
  .card__shape { position: absolute; inset: 0; width: 100%; height: 100%; }

  /* Front */
  .front-brand {
    position: absolute;
    left: 230px;
    top: 150px;
    display: flex;
    align-items: center;
    gap: 18px;
  }
  .front-brand__mark {
    width: 26px; height: 26px;
    background: var(--yellow);
  }
  .front-brand__name {
    color: var(--yellow);
    font-weight: 900;
    font-size: 38px;
    line-height: 1.05;
    letter-spacing: .5px;
  }
  .front-tagline {
    position: absolute;
    left: 40px;
    bottom: 34px;
    color: var(--yellow);
    font-weight: 900;
    font-size: 34px;
    letter-spacing: .3px;
  }

  /* Back */
  .back-brand {
    position: absolute;
    left: 50px;
    top: 150px;
    width: 270px;
    color: var(--navy-soft);
    font-weight: 700;
    font-size: 30px;
    line-height: 1.1;
    text-transform: uppercase;
    letter-spacing: 1px;
  }
  .contact {
    position: absolute;
    right: 36px;
    top: 40px;
    text-align: right;
    color: var(--white);
    font-size: 19px;
    line-height: 1.3;
  }
  .contact__name {
    color: var(--yellow);
    font-weight: 900;
    font-size: 21px;
  }
  .contact__title { margin-bottom: 34px; }
  .contact__line {
    display: flex;
    justify-content: flex-end;
    align-items: center;
    gap: 8px;
  }
  .contact__icon { width: 18px; height: 18px; flex: none; }
  .contact__address { margin-top: 34px; font-size: 21px; line-height: 1.3; }
</style>
</head>
<body>

<section class="card card--front" aria-label="Card front">
  <svg class="card__shape" viewBox="0 0 700 400" preserveAspectRatio="none" aria-hidden="true">
    <polygon points="0,240 640,0 700,0 700,400 0,400" fill="var(--navy)"/>
  </svg>
  <div class="front-brand">
    <span class="front-brand__mark"></span>
    <span class="front-brand__name">Halvorsen<br>Advisory Partners</span>
  </div>
  <p class="front-tagline">Halvorsen Advisory Partners</p>
</section>

<section class="card card--back" aria-label="Card back">
  <svg class="card__shape" viewBox="0 0 700 400" preserveAspectRatio="none" aria-hidden="true">
    <path d="M290,0 C385,90 395,260 350,400 L700,400 L700,0 Z" fill="var(--yellow-soft)"/>
    <path d="M312,0 C405,90 422,260 378,400 L700,400 L700,0 Z" fill="var(--navy)"/>
  </svg>

  <p class="back-brand">Halvorsen Advisory Partners</p>

  <div class="contact">
    <p class="contact__name">Dale Forsyth</p>
    <p class="contact__title">Office Manager</p>

    <p class="contact__line">555.204.7716
      <svg class="contact__icon" viewBox="0 0 24 24" aria-hidden="true"><path fill="var(--yellow)" d="M6.6 10.8a15 15 0 0 0 6.6 6.6l2.2-2.2a1 1 0 0 1 1-.25 11.4 11.4 0 0 0 3.6.57 1 1 0 0 1 1 1V20a1 1 0 0 1-1 1A17 17 0 0 1 3 4a1 1 0 0 1 1-1h3.5a1 1 0 0 1 1 1c0 1.25.2 2.45.57 3.6a1 1 0 0 1-.25 1z"/></svg>
    </p>
    <p class="contact__line">d.forsyth@hvadpt.us
      <svg class="contact__icon" viewBox="0 0 24 24" aria-hidden="true"><rect x="2" y="5" width="20" height="14" rx="1.5" fill="var(--yellow)"/><path d="M3 6l9 7 9-7" fill="none" stroke="var(--navy)" stroke-width="1.6"/></svg>
    </p>
    <p class="contact__line">www.hvadpt.com
      <svg class="contact__icon" viewBox="0 0 24 24" aria-hidden="true"><circle cx="12" cy="12" r="10" fill="var(--yellow)"/><g fill="none" stroke="var(--navy)" stroke-width="1.3"><ellipse cx="12" cy="12" rx="4.5" ry="10"/><line x1="2" y1="12" x2="22" y2="12"/><line x1="12" y1="2" x2="12" y2="22"/></g></svg>
    </p>

    <p class="contact__address">48730 212th Crescent<br>Tallow Ridge, NE 66091</p>
  </div>
</section>

</body>
</html>
```